Current website re-design to a updated look and feel.

We currently have a website www.brightlanefreight.com that we want to give an updated look and feel to. We are a logistics company that competes with Pellwick, Dm Harrowgate, Quill but on a smaller scale. We want something fresh and updated. We have two locations one in downtown Brookmere, IL and one in Palatine IL. We are a fun group that also gets the job done. We know we need pictures of both locations and possibly a video, but we need fresh design ideas. The 'who we are' page is really the only page that we currently want to keep. The 'what we do' page needs to be completely re-done from a look and feel for sure.

Target Market(s)

Anyone who uses Truck transportation to move their product. Mainly US manufacturers.

Industry/Entity Type

Logistics

Number of Pages Required

5+ page

Font styles to use
Sans Serif

Colors
5c91c4
0355a3
d0dfed

Requirements
Must have
• The new design must entice people to want to do business with us. The design must have locations for pictures and at least one video which we know we will have to provide. Design must be easy to navigate.

```html
<!DOCTYPE html>
<html lang="en">
<head>
<meta charset="utf-8">
<title>Brightlane Freight</title>
<link href="https://fonts.googleapis.com/css2?family=Lato:wght@400;700&family=Open+Sans:wght@400;600;700&display=swap" rel="stylesheet">
<style>
:root{
  --blue:#0355a3;
  --blue-mid:#5c91c4;
  --blue-pale:#d0dfed;
  --ink:#1f1f1f;
  --text:#555;
  --dark:#1b1f24;
  --white:#fff;
}
*{margin:0;padding:0;box-sizing:border-box}
html,body{width:1200px;height:2826px;overflow:hidden;background:var(--white)}
body{position:relative;font-family:"Open Sans",Arial,sans-serif;color:var(--text)}
.abs{position:absolute}
h1,h2,h3{font-family:"Lato",Arial,sans-serif;color:var(--ink)}

/* header */
.site-header{left:0;top:0;width:1200px;height:88px;background:var(--white)}
.brand{left:98px;top:24px;display:flex;align-items:center;gap:10px;font-family:"Open Sans",sans-serif;font-weight:700;font-size:24px;color:var(--blue)}
.brand-dot{width:26px;height:26px;border-radius:50%;background:var(--blue)}
.main-nav{left:370px;top:31px;display:flex;gap:23px;font-family:"Lato",sans-serif;font-size:17px;font-weight:700;color:#222}
.btn-chat{left:912px;top:24px;width:93px;height:37px;border-radius:19px;background:var(--blue);color:#fff;font-size:14px;font-weight:700;display:flex;align-items:center;justify-content:center;gap:6px}
.btn-login{left:1010px;top:24px;width:92px;height:37px;border-radius:19px;border:2px solid #d4d4d4;color:var(--blue);font-size:14px;font-weight:700;display:flex;align-items:center;justify-content:center;gap:6px}

/* hero */
.hero{left:0;top:88px;width:1200px;height:474px;background:linear-gradient(180deg,#3f5a7c 0%,#7d92a8 30%,#8a7b6a 55%,#5b6670 80%,#3d4a58 100%)}
.hero-title{left:0;top:168px;width:1200px;text-align:center;font-family:"Lato",sans-serif;font-weight:700;font-size:41px;color:#fff}
.play-btn{left:568px;top:430px;width:64px;height:64px}

/* welcome */
.welcome-title{left:0;top:616px;width:1200px;text-align:center;font-size:32px;font-weight:700}
.welcome-text{left:198px;top:678px;width:804px;text-align:center;font-size:13px;line-height:26px}
.btn-quote{left:503px;top:778px;width:195px;height:44px;border:2px solid #c9c9c9;border-radius:22px;color:var(--blue);font-size:15px;font-weight:700;display:flex;align-items:center;justify-content:center}

/* what we do */
.services-band{left:0;top:882px;width:1200px;height:221px;background:var(--blue)}
.services-title{left:0;top:918px;width:1200px;text-align:center;color:#fff;font-size:30px;font-weight:700}
.services-intro{left:200px;top:970px;width:800px;text-align:center;color:#fff;font-size:12px;line-height:24px}
.service{width:250px;text-align:center}
.service-icon{width:146px;height:146px;border-radius:50%;background:#fff;border:6px solid var(--blue);margin:0 auto;display:flex;align-items:center;justify-content:center}
.service h3{margin-top:30px;font-size:19px;font-weight:700}
.service p{margin-top:10px;font-size:12.5px;line-height:23px;height:69px;overflow:hidden}
.read-more{margin-top:14px;display:block;color:var(--blue);font-size:12.5px;font-weight:700}
.divider{left:98px;top:1406px;width:1004px;height:1px;background:#d6d6d6}

/* founder */
.founder-photo{left:98px;top:1470px;width:290px;height:382px;border:5px solid #e2e2e2;background:linear-gradient(180deg,#f4f4f4 0%,#e8e2d6 45%,#8f8a7c 100%)}
.founder-name{left:446px;top:1466px;font-size:30px;font-weight:700}
.founder-role{left:448px;top:1510px;font-family:"Lato",sans-serif;font-style:italic;font-weight:700;font-size:19px;color:var(--blue)}
.founder-text{left:448px;top:1556px;width:656px;font-size:12.5px;line-height:26px}
.founder-text p+p{margin-top:24px}
.signature{left:448px;top:1806px;width:170px;height:40px;background:linear-gradient(90deg,#e6e6e6,#f5f5f5)}

/* news */
.news{left:0;top:1925px;width:1200px;height:375px;background:linear-gradient(180deg,#dbe6f1,var(--blue-pale))}
.news-title{left:0;top:1975px;width:1200px;text-align:center;font-size:30px;font-weight:700}
.news-img{width:204px;height:180px;border:4px solid #fff;box-shadow:0 0 0 1px #c6d2de}
.news-body{width:260px}
.news-body h3{font-family:"Open Sans",sans-serif;font-size:15px;font-weight:700;color:#222}
.news-meta{margin-top:10px;font-size:12px;color:#666;display:flex;align-items:center;gap:6px}
.news-meta i{width:9px;height:9px;background:var(--blue);display:inline-block;border-radius:2px}
.news-body p{margin-top:10px;font-size:12px;line-height:22px}
.btn-news{margin-top:18px;width:126px;height:34px;border:2px solid #a9b9c9;border-radius:17px;color:var(--blue);font-size:12px;font-weight:700;display:flex;align-items:center;justify-content:center}

/* contact */
.contact{left:0;top:2300px;width:1200px;height:446px;background:linear-gradient(180deg,#262b31,#15181c)}
.contact-title{left:0;top:2340px;width:1200px;text-align:center;color:#fff;font-size:30px;font-weight:700}
.label{color:#fff;font-size:16px;font-weight:600}
.field{background:#fff;border:1px solid #ccc;color:#888;font-size:11px;padding:10px 10px}
.btn-submit{left:625px;top:2648px;width:79px;height:27px;border-radius:14px;background:var(--blue);color:#fff;font-size:12px;font-weight:700;display:flex;align-items:center;justify-content:center}
.info-row{left:782px;display:flex;align-items:center;gap:18px;color:#eee;font-size:12.5px}
.info-icon{width:32px;height:32px;border-radius:50%;border:1px solid #888;display:flex;align-items:center;justify-content:center}
.badge{top:2624px;height:62px}

/* footer */
.copyright{left:98px;top:2778px;font-size:11px;color:#555}
.social{top:2772px;width:29px;height:29px;border-radius:50%}
</style>
</head>
<body>

<header class="abs site-header">
  <div class="abs brand"><span class="brand-dot"></span>Brightlane</div>
  <nav class="abs main-nav"><span>What We Do</span><span>How We Do It</span><span>Who We Are</span><span>Tracking</span><span>Contact</span></nav>
  <div class="abs btn-chat">
    <svg width="14" height="12" viewBox="0 0 14 12"><path d="M1 1h12v7H6l-3 3V8H1z" fill="none" stroke="#fff" stroke-width="1.6"/></svg>CHAT</div>
  <div class="abs btn-login">
    <svg width="11" height="13" viewBox="0 0 11 13"><rect x="1" y="5" width="9" height="7" rx="1" fill="none" stroke="#0355a3" stroke-width="1.5"/><path d="M3 5V3.5a2.5 2.5 0 0 1 5 0V5" fill="none" stroke="#0355a3" stroke-width="1.5"/></svg>LOGIN</div>
</header>

<section class="abs hero" role="img" aria-label="Video still: port terminal with stacked shipping containers and cranes"></section>
<h1 class="abs hero-title">Transportation Distribution &amp; Warehousing</h1>
<svg class="abs play-btn" viewBox="0 0 64 64" aria-label="Play video"><circle cx="32" cy="32" r="30" fill="rgba(0,0,0,.35)" stroke="#fff" stroke-width="3"/><path d="M26 20l18 12-18 12z" fill="#fff"/></svg>

<h2 class="abs welcome-title">Welcome to Brightlane Freight</h2>
<p class="abs welcome-text">Brightlane vision is to be the premier third party logistics solution in North America. We will become premier by providing superior customer service, efficient and cost effective warehousing and distribution solutions. The decisions we make today for hiring, training, technology, strategic services and customer satisfaction are based on this vision.</p>
<div class="abs btn-quote">REQUEST A QUOTE</div>

<section class="abs services-band"></section>
<h2 class="abs services-title">What We Do</h2>
<p class="abs services-intro">Brightlane's mission is to provide the most thorough and satisfying third-party logistics experience for its customers. Brightlane uses leading technologies and an industry experienced staff to deliver an unparalleled customer service experience.</p>

<div class="abs service" style="left:78px;top:1052px">
  <div class="service-icon"><svg width="64" height="56" viewBox="0 0 64 56" fill="#5c91c4"><circle cx="32" cy="14" r="10"/><circle cx="12" cy="20" r="7"/><circle cx="52" cy="20" r="7"/><path d="M16 56V40a16 16 0 0 1 32 0v16z"/><path d="M0 52V38a11 11 0 0 1 14-10v24zM64 52V38a11 11 0 0 0-14-10v24z"/></svg></div>
  <h3>Freight Management</h3>
  <p>We strive for a perfect delivery &amp; promise to be there for anything you may need, every step of the way.</p>
  <span class="read-more">READ MORE &gt;&gt;</span>
</div>
<div class="abs service" style="left:342px;top:1052px">
  <div class="service-icon"><svg width="64" height="46" viewBox="0 0 64 46" fill="#5c91c4"><rect x="0" y="4" width="40" height="30" rx="3"/><path d="M42 14h12l10 12v8H42z"/><circle cx="12" cy="38" r="7" stroke="#fff" stroke-width="3"/><circle cx="52" cy="38" r="7" stroke="#fff" stroke-width="3"/></svg></div>
  <h3>Transportation</h3>
  <p>With a combined 500+ years of industry experience between all employees, we are the logistics company you can trust.</p>
  <span class="read-more">READ MORE &gt;&gt;</span>
</div>
<div class="abs service" style="left:606px;top:1052px">
  <div class="service-icon"><svg width="72" height="60" viewBox="0 0 72 60"><path d="M6 24L36 4l30 20v34H6z" fill="#0355a3"/><rect x="28" y="26" width="32" height="30" fill="#fff"/><path d="M30 30h28M30 36h28M30 42h28M30 48h28" stroke="#0355a3" stroke-width="2"/><rect x="4" y="38" width="16" height="14" fill="#5c91c4"/><path d="M20 45h8m-4-4l4 4-4 4" stroke="#5c91c4" stroke-width="3" fill="none"/></svg></div>
  <h3>Warehouse &amp; Distribution</h3>
  <p>Our secure facility can accommodate large or small quantities of product. Our inventory management system keeps track.</p>
  <span class="read-more">READ MORE &gt;&gt;</span>
</div>
<div class="abs service" style="left:870px;top:1052px">
  <div class="service-icon"><svg width="72" height="52" viewBox="0 0 72 52" fill="none" stroke="#0355a3" stroke-width="4"><path d="M10 6h40l6 20H4z"/><path d="M4 26h60v12H4z"/><path d="M30 26v-8h14"/><circle cx="16" cy="42" r="6" fill="#fff"/><circle cx="54" cy="42" r="6" fill="#fff"/></svg></div>
  <h3>Carriers</h3>
  <p>Are you a carrier looking to work with Brightlane? Click here to find out why we have the best carrier relationships.</p>
  <span class="read-more">READ MORE &gt;&gt;</span>
</div>

<div class="abs divider"></div>

<div class="abs founder-photo" role="img" aria-label="Portrait of the founder in a tweed jacket"></div>
<h2 class="abs founder-name">Marlene Ashby</h2>
<div class="abs founder-role">Founder</div>
<div class="abs founder-text">
  <p>Brightlane Freight welcomes you to our growing family of clients! We have over 26 years of experience in helping people solve their logistics needs from coast-to-coast. We also provide friendly, exceptional service that makes it easy to do business with us. Give us a call today and experience the difference for yourself!</p>
  <p>"Our service commitment begins from the moment you contact us. We appreciate your trust, and we go the extra mile to ensure that your freight is handled with care and expediency. If an issue comes up, we work tirelessly to resolve it, staying in contact with you until your freight is delivered without issue!"</p>
  <p>Let us take the worry out of your logistics. Relax, we've got this!</p>
</div>
<div class="abs signature" role="img" aria-label="Founder's handwritten signature"></div>

<section class="abs news"></section>
<h2 class="abs news-title">Latest News</h2>
<div class="abs news-img" style="left:98px;top:2057px;background:linear-gradient(180deg,#a9c6e2 0%,#c9d8e6 45%,#7a5a44 60%,#2c6e72 80%,#1f4c5a 100%)" role="img" aria-label="Container ship at sea"></div>
<div class="abs news-body" style="left:330px;top:2052px">
  <h3>FINIBUS BONORUM ET MALORUM</h3>
  <div class="news-meta"><i></i>08/03/2016 &nbsp;| <i></i>John Doe</div>
  <p>Nam libero tempore, cum soluta nobis est elig endi optio cumque nihil impedit quo minus id quod maxime placeat facere.</p>
  <div class="btn-news">READ MORE &gt;&gt;</div>
</div>
<div class="abs news-img" style="left:633px;top:2057px;background:linear-gradient(180deg,#d8dbe0 0%,#b9b4ac 40%,#c9a77c 70%,#a9845a 100%)" role="img" aria-label="Warehouse interior with stacked cartons"></div>
<div class="abs news-body" style="left:865px;top:2052px">
  <h3>FINIBUS BONORUM ET MALORUM</h3>
  <div class="news-meta"><i></i>08/03/2016 &nbsp;| <i></i>John Doe</div>
  <p>Nam libero tempore, cum soluta nobis est elig endi optio cumque nihil impedit quo minus id quod maxime placeat facere.</p>
  <div class="btn-news">READ MORE &gt;&gt;</div>
</div>

<section class="abs contact" role="img" aria-label="Dark background photo of a highway at dusk"></section>
<h2 class="abs contact-title">Contact Us</h2>
<div class="abs label" style="left:98px;top:2412px">Get In Touch:</div>
<div class="abs field" style="left:98px;top:2457px;width:299px;height:37px">NAME :</div>
<div class="abs field" style="left:407px;top:2457px;width:297px;height:37px">PHONE :</div>
<div class="abs field" style="left:98px;top:2506px;width:606px;height:37px">EMAIL :</div>
<div class="abs field" style="left:98px;top:2554px;width:606px;height:80px">MESSAGE :</div>
<div class="abs btn-submit">SUBMIT</div>

<div class="abs label" style="left:782px;top:2412px">Contact Information</div>
<div class="abs info-row" style="top:2471px"><span class="info-icon"><svg width="12" height="16" viewBox="0 0 12 16"><path d="M6 15S1 9 1 6a5 5 0 0 1 10 0c0 3-5 9-5 9z" fill="#fff"/><circle cx="6" cy="6" r="2" fill="#222"/></svg></span>Harlow Creek, IL &nbsp;60412 &nbsp;| &nbsp;Brookmere, IL</div>
<div class="abs info-row" style="top:2515px"><span class="info-icon"><svg width="14" height="14" viewBox="0 0 14 14"><path d="M3 1l3 3-2 2a8 8 0 0 0 4 4l2-2 3 3-2 2C6 13 1 8 1 3z" fill="#fff"/></svg></span>847.555.0142</div>
<div class="abs info-row" style="top:2559px"><span class="info-icon"><svg width="14" height="10" viewBox="0 0 14 10"><rect width="14" height="10" rx="1" fill="#fff"/><path d="M0 1l7 5 7-5" stroke="#222" fill="none"/></svg></span>info@brightlanefreight.com</div>
<div class="abs badge" style="left:786px;width:140px;background:#0d3b45;border:2px solid #5fa8b2;border-radius:6px" role="img" aria-label="Certification badge"></div>
<div class="abs badge" style="left:940px;width:140px;background:#fff" role="img" aria-label="Business ethics award badge"></div>

<div class="abs copyright">Copyrights © 2017, Brightlane Freight. All Rights Reserved.</div>
<div class="abs social" style="left:1006px;background:#2b4c8c" role="img" aria-label="Social link"></div>
<div class="abs social" style="left:1040px;background:#3aa4e0" role="img" aria-label="Social link"></div>
<div class="abs social" style="left:1074px;background:#d9322b" role="img" aria-label="Social link"></div>
<div class="abs social" style="left:1108px;background:#9a7a5a" role="img" aria-label="Social link"></div>

</body>
</html>
```